Deliver a professional and engaging investment propsal.

I am appealing to highend smart investors and need a high quality, engaging and formal presentation in PDF.
DropBox: https://www.filevarnel.net/sh/kq7tmrw2xz4pd8c/BBzRw7TfLpQsYnHuGe3rV9cXb?dl=0
Text for project is in Dropbox called New Proposal Final
Along with past much older attempts of this job.
Any additional ideas to enable a better outcome would be appreicated.

```html
<!DOCTYPE html>
<html lang="en">
<head>
<meta charset="utf-8">
<title>Major Site Change – Ridgeline Town Center</title>
<link href="https://fonts.googleapis.com/css2?family=Lato:wght@300;400;700&family=Fjalla+One&display=swap" rel="stylesheet">
<style>
:root{
  --page:#e8e9eb;
  --card:#ffffff;
  --blue:#1170c0;
  --blue-light:#3a97d6;
  --text:#5a5d62;
  --dark:#3c3f44;
}
*{margin:0;padding:0;box-sizing:border-box}
html,body{width:867px;height:1200px;overflow:hidden;background:var(--page)}
.page{position:relative;width:867px;height:1200px;font-family:"Lato",sans-serif;color:var(--text)}
.heading{position:absolute;left:97px;top:132px}
.heading-kicker{font-weight:300;font-size:28px;color:var(--text);line-height:1}
.heading-title{font-weight:700;font-size:36px;color:var(--blue);line-height:1;margin-top:3px;letter-spacing:.2px}
.heading-rule{position:absolute;left:97px;top:212px;width:673px;height:5px;background:var(--blue)}
.intro{position:absolute;left:97px;top:244px;width:675px;font-size:15px;line-height:19px}
.card{position:absolute;width:213px;height:221px;background:var(--card);border-bottom:8px solid var(--blue);text-align:center}
.card-figure{position:absolute;left:0;right:0;font-family:"Fjalla One",sans-serif;color:var(--blue);line-height:1}
.card-figure.large{top:48px;font-size:50px}
.card-figure.medium{top:42px;font-size:31px}
.card-icon{position:absolute;left:50%;transform:translateX(-50%);top:40px}
.card-divider{position:absolute;left:76px;width:61px;height:1px;background:var(--dark)}
.card-text{position:absolute;left:6px;right:6px;font-size:10px;line-height:14px;color:var(--text);white-space:nowrap}
.closing{position:absolute;left:77px;width:705px;font-size:15px;line-height:19px}
.footer-name{position:absolute;right:420px;top:1145px;font-size:15px;color:var(--dark);letter-spacing:.2px;white-space:nowrap}
.footer-bar{position:absolute;left:457px;top:1149px;width:410px;height:13px;background:var(--blue)}
.footer-bar::before{content:"";position:absolute;left:0;top:0;width:131px;height:13px;background:var(--blue-light)}
.footer-line{position:absolute;top:1168px;height:1.5px;background:var(--blue-light)}
.page-number{position:absolute;left:69px;top:1158px;font-size:15px;font-weight:700;color:var(--dark)}
</style>
</head>
<body>
<main class="page">
  <header class="heading">
    <div class="heading-kicker">Major</div>
    <h1 class="heading-title">SITE CHANGE</h1>
  </header>
  <div class="heading-rule"></div>
  <p class="intro">We purchased the property in in 2013 for cash and without any additional debt,at the time we had highway 85 frontage just outside Watford City limitsSouth of town with a zoning ofagricultural within McKenzie County.</p>

  <section class="card" style="left:77px;top:359px">
    <div class="card-figure large">2014</div>
    <div class="card-divider" style="top:131px"></div>
    <p class="card-text" style="top:163px">2014 site zoning changed<br>allowing a<br>commercial zoning.</p>
  </section>

  <section class="card" style="left:335px;top:359px">
    <svg class="card-icon" width="56" height="56" viewBox="0 0 56 56" aria-hidden="true">
      <rect x="6" y="2" width="44" height="4" fill="#1170c0"/>
      <rect x="4" y="6" width="48" height="50" fill="#1170c0"/>
      <g fill="#fff">
        <rect x="9" y="10" width="5" height="7"/><rect x="17" y="10" width="5" height="7"/><rect x="25" y="10" width="5" height="7"/><rect x="33" y="10" width="5" height="7"/><rect x="41" y="10" width="5" height="7"/>
        <rect x="9" y="22" width="5" height="7"/><rect x="17" y="22" width="5" height="7"/><rect x="25" y="22" width="5" height="7"/><rect x="33" y="22" width="5" height="7"/><rect x="41" y="22" width="5" height="7"/>
        <rect x="18" y="40" width="20" height="13"/>
      </g>
      <rect x="26" y="40" width="4" height="13" fill="#1170c0"/>
    </svg>
    <div class="card-divider" style="top:131px"></div>
    <p class="card-text" style="top:151px">Flag Hotel site purchased<br>2014 now with the option to<br>purchase the franchise license<br>and build the hotel ourselves.</p>
  </section>

  <section class="card" style="left:593px;top:359px">
    <svg class="card-icon" width="64" height="60" viewBox="0 0 64 60" aria-hidden="true">
      <path d="M40 2 C36 12 28 20 28 30 a12 12 0 0 0 24 0 C52 20 44 12 40 2Z" fill="#1170c0"/>
      <path d="M44 26 a7 7 0 0 1 -6 11" stroke="#fff" stroke-width="2.5" fill="none" stroke-linecap="round"/>
      <path d="M6 42 C14 40 20 42 26 46 C32 50 40 50 48 44 C44 54 34 58 24 56 C18 55 12 52 6 50Z" fill="#1170c0"/>
    </svg>
    <div class="card-divider" style="top:131px"></div>
    <p class="card-text" style="top:141px">In 2016 we were added into City<br>Limits which was a massive impro-<br>vement to our site now takingad<br>vantage of confirmed city water<br>and sewer was a great outcome.</p>
  </section>

  <section class="card" style="left:77px;top:621px">
    <div class="card-figure medium">100 YARDS</div>
    <div class="card-divider" style="top:111px"></div>
    <p class="card-text" style="top:120px">In 2016 the new bypass opened<br>intersecting our highway front<br>age just 100 yards away which<br>brings allthe traffic in the<br>Bakken right past our site which<br>was a massive win for this project.</p>
  </section>

  <section class="card" style="left:335px;top:621px">
    <div class="card-figure medium">$750,000</div>
    <div class="card-divider" style="top:111px"></div>
    <p class="card-text" style="top:127px">Same commercial property listed<br>across the road at $750,000 per<br>acre retail at Harlow Commonsand<br>other business parks<br>average listings $550,00 per acre</p>
  </section>

  <section class="card" style="left:593px;top:621px">
    <div class="card-figure medium">2017-18</div>
    <div class="card-divider" style="top:111px"></div>
    <p class="card-text" style="top:127px">In late 2017 we applied for full site<br>development application and were<br>approved in mid-2018 which again<br>was a significant improvement to<br>the project.</p>
  </section>

  <p class="closing" style="top:893px">May 2018Full site infrastructure development approval which includes all roads and city services, this will trigger interest in thesite from passing traffic and with a great marketing campaign will surely start sales coming in quickly once we break ground and start work.</p>
  <p class="closing" style="top:969px;width:780px">We also can buy the franchise license of the Summit Lodge hotel for additional income potential if desired.</p>

  <footer>
    <div class="footer-name">RIDGELINE TOWN CENTER</div>
    <div class="footer-bar"></div>
    <div class="footer-line" style="left:0;width:59px"></div>
    <div class="page-number">2</div>
    <div class="footer-line" style="left:91px;width:776px"></div>
  </footer>
</main>
</body>
</html>
```